Updated Business Card Re-design (Logo Provided)

I am needing to update our business cards for our practice, Brightfield Care Partners. We are a personal injury and wellness practice. The final design should be elegant and classy, but a type of card people would want to keep. Any samples should only have Dr. Tomas Verlinde on the template.
Updates

Went on vacation/holiday

Need extra days to review

Target Market(s)

Personal Injury clients, wellness clients

Industry/Entity Type

Personal Injury, medical, wellness

Contact Information for Business Card

dr and practice name, offerings

Requirements
Must have
• Single sided, this will be printed on a transparent business card, no exceptions.

```html
<!DOCTYPE html>
<html lang="en">
<head>
<meta charset="utf-8">
<title>Brightfield Care Partners – Business Card</title>
<link rel="stylesheet" href="https://fonts.googleapis.com/css2?family=Montserrat:wght@400;500;600;700;800&display=swap">
<style>
  :root {
    --page-bg: #e3e3e3;
    --card-bg: #f9f9f9;
    --brand-orange: #f59222;
    --brand-blue: #0a72bb;
    --brand-green: #2d8a4a;
    --ink: #1e1e1e;
    --white: #ffffff;
  }
  * { margin: 0; padding: 0; box-sizing: border-box; }
  html, body {
    width: 825px; height: 1200px; overflow: hidden;
    background: var(--page-bg);
    font-family: "Montserrat", sans-serif;
    color: var(--ink);
  }
  .business-card {
    position: absolute; left: 32px; top: 372px;
    width: 760px; height: 455px;
    background: var(--card-bg);
    overflow: hidden;
  }
  .brand {
    position: absolute; left: 28px; top: 46px;
    display: flex; align-items: center; gap: 10px;
  }
  .brand-dot { width: 26px; height: 26px; border-radius: 50%; background: var(--brand-blue); }
  .brand-name { font-weight: 700; font-size: 20px; color: var(--brand-blue); letter-spacing: -0.3px; white-space: nowrap; }
  .doctor-name {
    position: absolute; left: 29px; top: 144px;
    width: 345px;
    font-weight: 700; font-size: 26px; color: var(--brand-orange); letter-spacing: -0.2px;
    white-space: nowrap;
  }
  .associate {
    position: absolute; left: 30px; top: 182px;
    font-weight: 500; font-size: 16px; color: var(--ink); white-space: nowrap;
  }
  .contact-list { position: absolute; left: 30px; top: 228px; list-style: none; }
  .contact-item {
    display: flex; align-items: center; height: 36px;
    font-weight: 500; font-size: 18px; white-space: nowrap;
  }
  .contact-icon { width: 26px; height: 26px; margin-right: 22px; flex: none; }
  .services-panel {
    position: absolute; left: 384px; top: 1px;
    width: 346px; height: 346px;
    background: var(--brand-orange);
    color: var(--white);
  }
  .practice-title {
    position: absolute; left: 29px; top: 36px;
    font-weight: 800; font-size: 27px; line-height: 29px; letter-spacing: 0.3px;
    text-transform: uppercase;
  }
  .practice-sub { position: absolute; left: 29px; top: 98px; font-weight: 500; font-size: 20px; white-space: nowrap; }
  .service-list { position: absolute; left: 32px; top: 142px; list-style: none; }
  .service-item {
    display: flex; align-items: center; height: 37px;
    font-weight: 500; font-size: 20px; white-space: nowrap;
  }
  .service-icon { width: 22px; height: 22px; margin-right: 23px; flex: none; }
  .figure-art {
    position: absolute; left: 598px; top: 300px; width: 162px; height: 138px;
    background: linear-gradient(135deg, var(--brand-blue) 0%, var(--brand-blue) 45%, var(--brand-orange) 55%, var(--brand-orange) 100%);
    border-radius: 60% 40% 0 50%;
    opacity: 0.9;
  }
  .color-bar { position: absolute; left: 31px; top: 441px; height: 14px; display: flex; width: 704px; }
  .color-bar span { flex: 1; }
  .bar-blue { background: var(--brand-blue); }
  .bar-orange { background: var(--brand-orange); }
  .bar-green { background: var(--brand-green); }
</style>
</head>
<body>
<div class="business-card">
  <div class="brand">
    <span class="brand-dot"></span>
    <span class="brand-name">Brightfield Care Partners</span>
  </div>

  <h1 class="doctor-name">Dr. Tomas Verlinde, D.C.</h1>
  <p class="associate">Marcus L Renfield, PT, ATC, MS</p>

  <ul class="contact-list">
    <li class="contact-item">
      <svg class="contact-icon" viewBox="0 0 26 26"><circle cx="13" cy="13" r="13" fill="#0a72bb"/><path d="M9 7.5c.6-.5 1.4-.4 1.8.2l1.2 1.8c.3.5.2 1.1-.2 1.5l-.7.7c.7 1.5 1.8 2.7 3.3 3.4l.7-.7c.4-.4 1-.5 1.5-.2l1.8 1.2c.6.4.7 1.2.2 1.8l-.8.9c-.6.6-1.5.8-2.300.5-3.400-1.300-6-3.900-7.300-7.300-.3-.8-.1-1.700.5-2.300z" fill="#fff"/></svg>
      555.014.2281
    </li>
    <li class="contact-item">
      <svg class="contact-icon" viewBox="0 0 26 26"><circle cx="13" cy="13" r="13" fill="#0a72bb"/><rect x="9.5" y="6.5" width="7" height="13" rx="1.3" fill="none" stroke="#fff" stroke-width="1.6"/><circle cx="13" cy="17.2" r="0.8" fill="#fff"/></svg>
      555.018.6437
    </li>
    <li class="contact-item">
      <svg class="contact-icon" viewBox="0 0 26 26"><circle cx="13" cy="13" r="13" fill="#0a72bb"/><rect x="7" y="9" width="12" height="8.5" fill="none" stroke="#fff" stroke-width="1.4"/><path d="M7 9l6 5 6-5M7 17.5l4.5-4M19 17.5l-4.5-4" fill="none" stroke="#fff" stroke-width="1.2"/></svg>
      hello@brightfieldcare.com
    </li>
    <li class="contact-item">
      <svg class="contact-icon" viewBox="0 0 26 26"><circle cx="13" cy="13" r="13" fill="#0a72bb"/><rect x="7" y="9" width="12" height="8.5" fill="none" stroke="#fff" stroke-width="1.4"/><path d="M7 9l6 5 6-5M7 17.5l4.5-4M19 17.5l-4.5-4" fill="none" stroke="#fff" stroke-width="1.2"/></svg>
      www.brightfieldcare.com
    </li>
  </ul>

  <section class="services-panel">
    <h2 class="practice-title">Brightfield Care<br>Partners</h2>
    <p class="practice-sub">Peachtree Spine Center</p>
    <ul class="service-list">
      <li class="service-item"><svg class="service-icon" viewBox="0 0 22 22"><circle cx="11" cy="11" r="11" fill="#fff"/><path d="M11 6v10M6 11h10" stroke="#f59222" stroke-width="2.4"/></svg>Auto Accident Care</li>
      <li class="service-item"><svg class="service-icon" viewBox="0 0 22 22"><circle cx="11" cy="11" r="11" fill="#fff"/><path d="M11 6v10M6 11h10" stroke="#f59222" stroke-width="2.4"/></svg>Primary Care</li>
      <li class="service-item"><svg class="service-icon" viewBox="0 0 22 22"><circle cx="11" cy="11" r="11" fill="#fff"/><path d="M11 6v10M6 11h10" stroke="#f59222" stroke-width="2.4"/></svg>Medical Weight loss</li>
      <li class="service-item"><svg class="service-icon" viewBox="0 0 22 22"><circle cx="11" cy="11" r="11" fill="#fff"/><path d="M11 6v10M6 11h10" stroke="#f59222" stroke-width="2.4"/></svg>Physical Therapy</li>
      <li class="service-item"><svg class="service-icon" viewBox="0 0 22 22"><circle cx="11" cy="11" r="11" fill="#fff"/><path d="M11 6v10M6 11h10" stroke="#f59222" stroke-width="2.4"/></svg>Chiropractic</li>
    </ul>
  </section>

  <div class="figure-art" role="img" aria-label="Stylised running figure in blue and orange"></div>

  <div class="color-bar">
    <span class="bar-blue"></span>
    <span class="bar-orange"></span>
    <span class="bar-green"></span>
  </div>
</div>
</body>
</html>
```